Web design for facial expression recognition service

We offer a service which allows customers to film large panels of participants looking at some video/screen (e.g. an advertisement) and to analyze the facial expressions shown by the participants. We are looking for the design of a new website which will make it easy for our customers to setup and view the results of these experiments online.
Competitor's websites that may serve as a reference are:
http://www.moriventa.com/quelbo/#pane_overview
http://www.dunvarpix.com/homepage.aspx
https://www.tamlora.com/
The website will (for as far as the design is concerned) consist of three parts:
- A public home page (and perhaps some contact/news/about page), designed to catch the attention/interest potential customers.
- A (protected) project result page, showing the results in an interactive page with charts and numerical data.
- Pages (also protected) with fields and tables (setting up the project details).
The winner of this design project should provide us with at least one design for each of the above in order to get a complete 'theme' going which our developers can use. However, you are welcome to initially only provide the design for the project result page and/or home page.
We are looking for a modern, fresh, yet professional look (my client is a more established party in the field).
The final delivery should consist of layered Photoshop or Illustrator files.
Thank you in advance for participating!
Updates
Dear designers,
Project Deadline Extended
Reason: Extending the deadline by a few days to give designers a chance to submit designs for the other pages and process further feedback.
Target Market(s)
marketing research agencies (B2B service)
Requirements
Must have
- Home page:
- Basic advertisement of the service; some quick explanation of how it works
- A way to login for existing users
- A link/button/banner inviting people to sign up
- Navigation controls to 2-3 other pages
- Social media links (plain social square, plain social square group)
- Company logo (sorry, can't provide it as my client wishes to remain anonymous for now, but it's rounded and has blue as it's main color).
- Copyright / creator details
Project result page:
(see attachment 1 for a functional mockup - the design may follow this layout closely, or be completely different)
- Title
- A video player and basic numerical data
- Different views of the analysis results can dynamically be added/removed/collapsed/expanded; each one of these views will show some kind of chart, filters (combos), numerical data and a download button/link.
- A way to sign out, go to the main project page and go to the main page
- Logo
- Copyright
The form pages:
(see attachment 2 for a functional mockup of one of the pages; feel free to change some elements to better show the overall style)
- Title
- Text fields, combos, calendar pickers, tables, navigation links
- Logo
- Copyright
Nice to have
- Any creative text elements or product logo/symbol are a bonus. However, the basic "Lorem Ipsum" would do too.

```html
<!DOCTYPE html>
<html lang="en">
<head>
<meta charset="utf-8">
<title>Velmarsh – Facial Expression Analysis</title>
<link href="https://fonts.googleapis.com/css2?family=PT+Sans:ital,wght@0,400;0,700;1,400;1,700&family=Roboto+Condensed:wght@400;700&display=swap" rel="stylesheet">
<style>
:root{
  --blue:#0a78c6;
  --blue-dark:#06599a;
  --blue-deep:#03508d;
  --blue-light:#47b6ee;
  --cyan:#2ec6f2;
  --topbar:#3a3a3a;
  --text:#555;
  --heading:#0b6aa8;
  --red:#c8101a;
  --green:#8ccf10;
  --white:#fff;
}
*{margin:0;padding:0;box-sizing:border-box}
html,body{width:1190px;height:1200px;overflow:hidden;background:#fff;font-family:"PT Sans",sans-serif;color:var(--text)}
.page{position:relative;width:1190px;height:1200px}
.abs{position:absolute}

/* top bar */
.topbar{left:0;top:0;width:1190px;height:43px;background:linear-gradient(#4a4a4a,#2c2c2c)}
.toplinks{left:742px;top:14px;font-size:10px;color:#bbb;display:flex;gap:24px;white-space:nowrap}
.login{left:936px;top:8px;width:74px;height:27px;border-radius:4px;background:linear-gradient(#2a2a2a,#1a1a1a);border:1px solid #555;color:#ddd;font-size:12px;line-height:25px;padding-left:14px}
.login span{position:absolute;right:10px;top:7px;width:12px;height:12px;border-radius:50%;background:#eee}
.login span::after{content:"";position:absolute;left:3px;top:3px;width:4px;height:4px;border-right:1.5px solid #222;border-bottom:1.5px solid #222;transform:rotate(45deg)}

/* hero */
.hero{left:0;top:43px;width:1190px;height:447px;background:linear-gradient(180deg,#0b6fbe 0%,#0d7fcf 55%,#2c9be0 80%,#56b9ee 100%)}
.hero-floor{left:0;top:418px;width:1190px;height:72px;background:linear-gradient(#3aa3e6,#5cbcf0)}
.logo{left:178px;top:90px;font:700 30px "PT Sans",sans-serif;color:var(--cyan);letter-spacing:-.5px}
.logo-dot{left:330px;top:58px;width:62px;height:62px;border-radius:50%;background:var(--cyan);opacity:.9}
.nav{left:472px;top:60px;display:flex;font-size:12.5px;font-weight:700;color:#fff}
.nav a{color:#fff;text-decoration:none;display:block;padding:6px 16px;margin-right:22px}
.nav a.active{background:linear-gradient(#1b86d4,#0d5fa6);border:2px solid #0a3d6b;border-radius:8px;box-shadow:0 0 0 1px #3fa0e4 inset}
.h1{left:178px;top:178px;font:italic 700 30px/31px "PT Sans",sans-serif;color:#fff;letter-spacing:-1px}
.h2{left:178px;top:253px;font:italic 700 19px/24px "PT Sans",sans-serif;color:#fff;letter-spacing:-.6px}
.lead{left:180px;top:312px;width:390px;font-size:8.8px;line-height:15.3px;color:#fff}
.signup{left:185px;top:395px;width:184px;height:33px;border-radius:17px;background:linear-gradient(#d8f56a,#8fcf12 55%,#6aa80a);border:2px solid #b9ea3a;box-shadow:0 6px 10px rgba(140,210,20,.6);font:700 15px/29px "PT Sans",sans-serif;color:#2e4d00;padding-left:24px}
.signup svg{position:absolute;right:12px;top:8px}
.monitor{left:600px;top:132px;width:410px;height:257px;border-radius:7px;background:#111;border:2px solid #d8d8d8}
.screen{left:15px;top:13px;width:377px;height:227px;border-radius:5px;background:linear-gradient(90deg,#d8c7a6,#e7c6ae 30%,#e3b9a3 50%,#e7c6ae 70%,#d6c39f)}
.stand{left:738px;top:389px;width:126px;height:70px}
.dots{left:954px;top:466px;display:flex;gap:5px}
.dots i{width:10px;height:10px;border-radius:50%;background:#8a8a8a;display:block}
.dots i.on{background:var(--cyan)}

/* how it works */
.how-title{left:178px;top:530px;font:italic 700 25px "PT Sans",sans-serif;color:var(--heading);letter-spacing:-1px}
.how-text{left:178px;top:568px;width:200px;font-size:8.8px;line-height:15.3px;color:#555}
.step{top:519px;width:205px;height:121px;background:linear-gradient(#d8d8d8,#c2c2c2);border-radius:3px}
.step.first{background:linear-gradient(#1588d6,#0a67b0)}
.step .num{position:absolute;left:14px;top:20px;font:700 66px/1 "Roboto Condensed",sans-serif;letter-spacing:-4px;color:#6b6b6b}
.step.first .num{color:#fff}
.step .t{position:absolute;left:84px;top:29px;font-size:10.5px;color:var(--heading)}
.step.first .t,.step.first .d{color:#fff}
.step .d{position:absolute;left:84px;top:50px;width:115px;font-size:8.6px;line-height:15.3px;color:#666}
.step .notch{position:absolute;right:-10px;top:50px;width:0;height:0;border-top:10px solid transparent;border-bottom:10px solid transparent;border-left:10px solid #0b6bb4;z-index:2}

/* video section */
.vsec{left:178px;top:661px;width:834px;height:215px;background:linear-gradient(#dcdcdc,#f2f2f2 40%,#fff)}
.player{left:197px;top:683px;width:307px;height:193px;background:#0b0f18;border:1px solid #555}
.pframe{left:4px;top:4px;width:297px;height:163px;background:linear-gradient(135deg,#1b2b45,#14233b 50%,#0f1a2d)}
.play{left:120px;top:62px;width:62px;height:62px;border-radius:50%;background:radial-gradient(#444,#1a1a1a);border:2px solid #555}
.play::after{content:"";position:absolute;left:23px;top:16px;border-left:22px solid #ccc;border-top:13px solid transparent;border-bottom:13px solid transparent}
.controls{left:0;top:170px;width:305px;height:22px;background:linear-gradient(#333,#111);font-size:9px;color:#ddd}
.vs-title{left:530px;top:703px;font:italic 700 20px "PT Sans",sans-serif;color:var(--red);letter-spacing:-1px}
.vs-sub{left:530px;top:728px;font:italic 700 16px "PT Sans",sans-serif;color:var(--heading);letter-spacing:-.6px}
.vs-body{left:530px;top:759px;width:466px;font-size:8.8px;line-height:15.3px;color:#555}

/* quotes */
.qhead{left:178px;top:900px;width:834px;height:42px;background:linear-gradient(#ededed,#fff)}
.q-title{left:197px;top:910px;font:italic 700 22px "PT Sans",sans-serif;color:var(--heading);letter-spacing:-1px}
.arrows{left:969px;top:913px;display:flex;gap:3px}
.arrows span{width:14px;height:18px;border:1px solid #aaa;border-radius:2px;background:linear-gradient(#fff,#ddd);position:relative}
.quote{top:963px;width:232px}
.quote .mk{position:absolute;left:-20px;top:-6px;font:italic 700 22px "PT Sans",sans-serif;color:#bbb}
.quote .mk2{position:absolute;right:-10px;top:66px;font:italic 700 22px "PT Sans",sans-serif;color:#bbb}
.quote h4{font-size:12.3px;font-weight:400;color:var(--heading);margin-bottom:5px}
.quote p{font-size:8.8px;line-height:15.3px;color:#555}
.client{top:1055px;display:flex;align-items:center;gap:10px}
.client .badge{width:81px;height:37px;border:1px solid #ccc;border-radius:3px;background:#fff;display:flex;align-items:center;justify-content:center;gap:5px;font-size:14px;color:#2b4f7a}
.client .badge i{width:9px;height:9px;background:#2b4f7a;display:block}
.client .who b{display:block;font-weight:400;font-size:12px;color:var(--red)}
.client .who em{font-size:9.5px;color:#888}

/* footer */
.footer{left:0;top:1125px;width:1190px;height:75px;background:var(--blue-deep)}
.fnav{left:178px;top:1146px;font-size:9.2px;color:#fff;display:flex}
.fnav span{padding:0 15px;border-left:1px solid #fff}
.fnav span:first-child{padding-left:0;border:0}
.copy{left:178px;top:1168px;font-size:9.2px;color:#fff}
.copy b{font-weight:400;color:var(--blue-light)}
.social-label{left:860px;top:1148px;width:90px;text-align:right;font-size:9.2px;line-height:15px;color:#fff}
.social{top:1149px;width:22px;height:22px;border-radius:4px;background:linear-gradient(#5aa4e0,#2a6fb8);border:1px solid #9cc8ef}
</style>
</head>
<body>
<div class="page">

  <header class="abs topbar"></header>
  <div class="abs toplinks"><span>Home</span><span>|</span><span>Help</span><span>|</span><span>Sitemap</span></div>
  <div class="abs login">Login<span></span></div>

  <section class="abs hero"></section>
  <div class="abs hero-floor"></div>
  <div class="abs logo-dot"></div>
  <div class="abs logo">Velmarsh</div>
  <nav class="abs nav">
    <a class="active">Home</a><a>About Us</a><a>Team</a><a>Videos</a><a>Clients</a><a>Contact Us</a>
  </nav>
  <h1 class="abs h1">We are a facial recognition<br>analysis company</h1>
  <h2 class="abs h2">We make group of 10 users see a video and analyse<br>their facial expressions</h2>
  <p class="abs lead">Lorem Ipsum is simply dummy text of the printing and typesetting industry. Lorem Ipsum has been the industry's standard dummy text ever since the 1500s, when an unknown printer took a galley of type and scrambled it to make a type specimen book.</p>
  <div class="abs signup">People to Signup
    <svg width="14" height="16" viewBox="0 0 14 16"><path d="M4 0h6v8h4l-7 8-7-8h4z" fill="#2e4d00"/></svg>
  </div>

  <div class="abs monitor">
    <div class="abs screen" role="img" aria-label="Photo of a face with facial analysis guide lines"></div>
  </div>
  <svg class="abs stand" viewBox="0 0 126 70">
    <defs><linearGradient id="st" x1="0" x2="1"><stop offset="0" stop-color="#9a9a9a"/><stop offset=".5" stop-color="#f4f4f4"/><stop offset="1" stop-color="#8a8a8a"/></linearGradient></defs>
    <path d="M22 0h82l4 50q18 6 10 12H8q-8-6 10-12z" fill="url(#st)"/>
  </svg>
  <div class="abs dots"><i class="on"></i><i></i><i></i><i></i></div>

  <h2 class="abs how-title">How it works</h2>
  <p class="abs how-text">Lorem Ipsum is simply dummy text of the printing and typesetting industry. Lorem Ipsum has been the industry's standard dummy text ever since the 1500s</p>

  <div class="abs step first" style="left:395px"><span class="notch"></span><span class="num">01</span><span class="t">Lorem Ipsum is simply</span><span class="d">Lorem Ipsum is simply dummy text of the printing and typesetting industry.</span></div>
  <div class="abs step" style="left:601px"><span class="num">02</span><span class="t">Lorem Ipsum is simply</span><span class="d">Lorem Ipsum is simply dummy text of the printing and typesetting industry.</span></div>
  <div class="abs step" style="left:807px"><span class="num">03</span><span class="t">Lorem Ipsum is simply</span><span class="d">Lorem Ipsum is simply dummy text of the printing and typesetting industry.</span></div>

  <section class="abs vsec"></section>
  <div class="abs player">
    <div class="abs pframe" role="img" aria-label="Video still of a face with analysis tracking overlay"></div>
    <div class="abs play"></div>
    <div class="abs controls">
      <svg class="abs" style="left:8px;top:6px" width="10" height="10"><rect width="3" height="10" fill="#ccc"/><rect x="6" width="3" height="10" fill="#ccc"/></svg>
      <span class="abs" style="left:55px;top:5px">0:04 / 0:30</span>
      <div class="abs" style="left:114px;top:9px;width:150px;height:5px;background:#444"></div>
      <div class="abs" style="left:114px;top:9px;width:44px;height:5px;background:#888"></div>
      <div class="abs" style="left:139px;top:6px;width:11px;height:11px;border-radius:50%;background:#eee"></div>
    </div>
  </div>
  <h3 class="abs vs-title">WE MAKE GROUP OF</h3>
  <p class="abs vs-sub">10 users see a video and analyse their facial expressions Welcome to Velmarsh</p>
  <div class="abs vs-body">
    <p>Lorem Ipsum is simply dummy text of the printing and typesetting industry. Lorem Ipsum has been the industry's standard dummy text ever since the 1500s, when an unknown printer took a galley of type and scrambled it to make a type specimen book. It has survived not only five centuries, but also the leap into electronic typesetting, remaining essentially unchanged.</p>
    <p style="margin-top:15px">It was popularised in the 1960s with the release of Brantix sheets containing Lorem Ipsum passages, and more recently with desktop publishing software.</p>
  </div>

  <div class="abs qhead"></div>
  <h2 class="abs q-title">Client Quotes</h2>
  <div class="abs arrows"><span></span><span></span></div>

  <div class="abs quote" style="left:218px"><span class="mk">“</span><h4>Lorem Ipsum is simply dummy</h4><p>Lorem Ipsum is simply dummy text of the printing and typesetting industry. Lorem Ipsum has been the industry's standard dummy text ever since the 1500s.</p><span class="mk2">”</span></div>
  <div class="abs quote" style="left:493px"><span class="mk">“</span><h4>Lorem Ipsum is simply dummy</h4><p>Lorem Ipsum is simply dummy text of the printing and typesetting industry. Lorem Ipsum has been the industry's standard dummy text ever since the 1500s.</p><span class="mk2">”</span></div>
  <div class="abs quote" style="left:776px"><span class="mk">“</span><h4>Lorem Ipsum is simply dummy</h4><p>Lorem Ipsum is simply dummy text of the printing and typesetting industry. Lorem Ipsum has been the industry's standard dummy text ever since the 1500s.</p><span class="mk2">”</span></div>

  <div class="abs client" style="left:217px"><div class="badge">Harlowe<i></i></div><div class="who"><b>Marlon Keyes</b><em>Organiser</em></div></div>
  <div class="abs client" style="left:492px"><div class="badge">Brisco</div><div class="who"><b>Marlon Keyes</b><em>Organiser</em></div></div>
  <div class="abs client" style="left:775px"><div class="badge"><i></i>Torvane</div><div class="who"><b>Marlon Keyes</b><em>Organiser</em></div></div>

  <footer class="abs footer"></footer>
  <div class="abs fnav"><span>Home</span><span>About Us</span><span>Team</span><span>Videos</span><span>Clients</span><span>Contact Us</span></div>
  <div class="abs copy">Copyright ©2013. <b>Velmarsh.</b> All rights reserved.</div>
  <div class="abs social-label">Connect to<br>our Social Network :</div>
  <a class="abs social" style="left:961px" aria-label="Social network link"></a>
  <a class="abs social" style="left:988px" aria-label="Professional network group link"></a>

</div>
</body>
</html>
```